TALVORE GROUP OF CLINICS

We need a medical & lab report file. The design should be healthcare related. Our current file design has been used for almost 10 years. We need something more fresh & up-to-date. We have attached the current file design.

Need extra days to review

```html
<!DOCTYPE html>
<html lang="en">
<head>
<meta charset="utf-8">
<title>Talvore Group of Clinics – Medical Report Folder</title>
<link href="https://fonts.googleapis.com/css2?family=Open+Sans:wght@400;600;700;800&family=Nunito:wght@900&family=Cormorant+Garamond:ital,wght@1,600&display=swap" rel="stylesheet">
<style>
  :root {
    --navy: #2a2f8f;
    --royal: #1f6fc8;
    --sky: #3aa8e6;
    --pale-sky: #5cc3f0;
    --gold: #f2b51a;
    --white: #ffffff;
    --grey-light: #f1f2f4;
    --grey-mid: #c9ccd1;
    --ink: #333840;
    --page-bg: #dcdde0;
  }
  * { box-sizing: border-box; margin: 0; padding: 0; }
  html, body { width: 1200px; height: 847px; overflow: hidden; background: var(--page-bg); }
  body { font-family: "Open Sans", Arial, sans-serif; }

  .folder { position: relative; width: 1200px; height: 847px; display: flex; }
  .page { position: relative; width: 600px; height: 847px; overflow: hidden; background: var(--white); }
  .page-art { position: absolute; inset: 0; }

  .brand { position: absolute; display: flex; align-items: center; gap: 8px; }
  .brand-dot { width: 16px; height: 16px; border-radius: 50%; background: var(--white); }
  .brand-name { font-weight: 800; font-size: 16px; color: var(--white); letter-spacing: .5px; }

  /* back cover */
  .group-ribbon {
    position: absolute; left: 300px; top: 118px; transform: rotate(-14deg); transform-origin: left top;
    background: var(--white); color: var(--navy); font-weight: 800; font-size: 16px;
    padding: 5px 14px; border-left: 6px solid var(--navy); box-shadow: 2px 3px 6px rgba(0,0,0,.25);
    white-space: nowrap;
  }
  .clinic-card {
    position: absolute; width: 250px; padding: 8px 12px 9px;
    transform: rotate(-12deg); transform-origin: left center;
    background: linear-gradient(180deg, var(--grey-light), var(--grey-mid));
    border-bottom: 3px solid var(--navy);
    box-shadow: 2px 3px 6px rgba(0,0,0,.2);
    text-align: right; color: var(--ink);
  }
  .clinic-card.right { text-align: left; }
  .clinic-name { font-size: 9.5px; font-weight: 700; color: var(--royal); white-space: nowrap; }
  .clinic-details { font-size: 7.2px; line-height: 1.3; white-space: nowrap; }

  /* front cover */
  .report-title {
    position: absolute; left: 70px; top: 222px; width: 500px; transform: rotate(-5deg);
    font-family: "Nunito", Arial, sans-serif; font-weight: 900; font-size: 46px; color: var(--navy);
    text-align: center; letter-spacing: -1px; white-space: nowrap;
    text-shadow: 2px 0 var(--white), -2px 0 var(--white), 0 2px var(--white), 0 -2px var(--white), 3px 4px 6px rgba(0,0,0,.3);
  }
  .tagline {
    position: absolute; left: 100px; top: 298px; width: 400px; transform: rotate(-5deg);
    font-family: "Cormorant Garamond", Georgia, serif; font-style: italic; font-weight: 600;
    font-size: 26px; color: var(--white); text-align: center; white-space: nowrap;
  }
  .confidential {
    position: absolute; left: 40px; top: 772px; transform: rotate(-3deg);
    font-weight: 600; font-size: 21px; color: var(--royal); letter-spacing: .5px; white-space: nowrap;
  }
</style>
</head>
<body>
<main class="folder">

  <section class="page back-cover">
    <svg class="page-art" width="600" height="847" viewBox="0 0 600 847">
      <defs>
        <linearGradient id="backHeader" x1="0" y1="0" x2="1" y2="1">
          <stop offset="0" stop-color="#3aa8e6"/><stop offset="1" stop-color="#2a62c4"/>
        </linearGradient>
        <linearGradient id="photoTone" x1="0" y1="0" x2="1" y2="1">
          <stop offset="0" stop-color="#e8e9ec"/><stop offset="1" stop-color="#f8f8f9"/>
        </linearGradient>
        <linearGradient id="waveBlue" x1="0" y1="0" x2="1" y2="0">
          <stop offset="0" stop-color="#1f6fc8"/><stop offset="1" stop-color="#2a3f9f"/>
        </linearGradient>
      </defs>
      <rect x="0" y="250" width="600" height="540" fill="url(#photoTone)" role="img" aria-label="Soft grey medical photograph of a doctor with stethoscope"/>
      <polygon points="0,110 600,0 600,160 0,340" fill="url(#backHeader)"/>
      <circle cx="115" cy="210" r="120" fill="#5cc3f0" opacity=".6"/>
      <polygon points="0,100 600,-10 600,0 0,110" fill="#f2b51a"/>
      <polygon points="0,340 600,160 600,168 0,350" fill="#f2b51a"/>
      <path d="M0,770 C200,750 420,690 600,570 L600,847 L0,847 Z" fill="#3aa8e6"/>
      <path d="M0,792 C220,772 430,712 600,610 L600,847 L0,847 Z" fill="url(#waveBlue)"/>
      <path d="M0,780 C220,760 430,700 600,594 L600,604 C430,710 220,772 0,792 Z" fill="#f2b51a"/>
      <path d="M0,815 C250,800 450,760 600,690 L600,847 L0,847 Z" fill="#2a62c4"/>
      <path d="M0,825 L600,810 L600,847 L0,847 Z" fill="#5cc3f0"/>
    </svg>

    <div class="brand" style="left:60px; top:220px;">
      <span class="brand-dot"></span><span class="brand-name">TALVORE GROUP</span>
    </div>
    <div class="group-ribbon">TALVORE GROUP OF CLINICS</div>

    <div class="clinic-list">
      <article class="clinic-card" style="left:20px; top:405px;">
        <h3 class="clinic-name">PUSAT PERUBATAN TALVORE</h3>
        <p class="clinic-details">Suite 8-3, Wisma Cendana, No. 27,<br>Jalan Seri Damai, 50470 Kuala Lumpur.<br>Tel: +603-5550-1101 Fax: +603-5550-1102<br>Email: pusat@talvore-clinics.example</p>
      </article>
      <article class="clinic-card right" style="left:320px; top:335px;">
        <h3 class="clinic-name">KLINIK TALVORE (BUKIT HALIA)</h3>
        <p class="clinic-details">No. 42, Jalan Halia 5, Bukit Halia,<br>40680 Shah Alam, Selangor.<br>Tel: +603-5550-9101 Fax: +603-5550-9102<br>Email: halia@talvore-clinics.example</p>
      </article>
      <article class="clinic-card right" style="left:320px; top:415px;">
        <h3 class="clinic-name">KLINIK TALVORE (SERI MERBAU)</h3>
        <p class="clinic-details">No. 55, Jalan Merbau Utama 1,<br>71990 Bandar Seri Merbau, Negeri Sembilan.<br>Tel: +606-555-3700 Fax: +606-555-3707<br>Email: merbau@talvore-clinics.example</p>
      </article>
      <article class="clinic-card" style="left:20px; top:490px;">
        <h3 class="clinic-name">KLINIK TALVORE (TELUK SENJA)</h3>
        <p class="clinic-details">No. 9, Lorong Kenari 2, Taman Senja,<br>11960 Teluk Senja, Pulau Kenari.<br>Tel: +604-555-6524 Fax: +604-555-6525<br>Email: senja@talvore-clinics.example</p>
      </article>
      <article class="clinic-card right" style="left:320px; top:495px;">
        <h3 class="clinic-name">TALVORE MEDICAL CLINIC (AIRPORT 2)</h3>
        <p class="clinic-details">Unit 3-07, Gate Plaza East,<br>43980 Padang Rimba, Selangor.<br>Tel: +603-5558-5909 Fax: +603-5558-5902<br>Email: airport2@talvore-clinics.example</p>
      </article>
      <article class="clinic-card" style="left:20px; top:575px;">
        <h3 class="clinic-name">TALVORE MEDICAL CLINIC (AIRPORT)</h3>
        <p class="clinic-details">Unit G-14, Arrivals Hall, North Concourse,<br>43970 Padang Rimba, Selangor.<br>Tel: +603-5557-5909 Fax: +603-5557-5901<br>Email: airport@talvore-clinics.example</p>
      </article>
      <article class="clinic-card" style="left:175px; top:650px;">
        <h3 class="clinic-name">TALVORE MEDICAL CLINIC (ISLAND AIRPORT)</h3>
        <p class="clinic-details">Unit 1-22, Departure Wing,<br>Pulau Kenari Airport, 11960 Teluk Senja.<br>Tel: +604-555-7101 Fax: +604-555-8102<br>Email: island@talvore-clinics.example</p>
      </article>
    </div>
  </section>

  <section class="page front-cover">
    <svg class="page-art" width="600" height="847" viewBox="0 0 600 847">
      <defs>
        <linearGradient id="frontBand" x1="0" y1="0" x2="1" y2="1">
          <stop offset="0" stop-color="#2f8fdc"/><stop offset="1" stop-color="#2a55b8"/>
        </linearGradient>
        <linearGradient id="photoToneFront" x1="0" y1="0" x2="1" y2="1">
          <stop offset="0" stop-color="#e6e7ea"/><stop offset="1" stop-color="#f9f9fa"/>
        </linearGradient>
      </defs>
      <rect x="0" y="400" width="600" height="360" fill="url(#photoToneFront)" role="img" aria-label="Faint grey illustration of human kidneys with a stethoscope"/>
      <polygon points="0,20 600,110 600,340 0,440" fill="url(#frontBand)"/>
      <circle cx="130" cy="140" r="110" fill="#5cc3f0" opacity=".7"/>
      <polygon points="0,290 600,260 600,300 0,330" fill="#3aa8e6" opacity=".8"/>
      <polygon points="0,12 600,100 600,112 0,24" fill="#f2b51a"/>
      <polygon points="0,440 600,340 600,350 0,450" fill="#f2b51a"/>
      <polygon points="520,355 600,340 600,400 560,560 500,460" fill="#2a62c4" stroke="#f2b51a" stroke-width="6" stroke-linejoin="round"/>
      <polygon points="0,760 600,740 600,756 0,776" fill="#2a3f9f" opacity=".15"/>
    </svg>

    <div class="brand" style="left:70px; top:140px;">
      <span class="brand-dot"></span><span class="brand-name">TALVORE GROUP</span>
    </div>
    <h1 class="report-title">MEDICAL REPORT</h1>
    <p class="tagline">“Your Healthcare Partner”</p>
    <p class="confidential">PRIVATE &amp; CONFIDENTIAL</p>
  </section>

</main>
</body>
</html>
```